A clean crisp business card for a Landscape Construction company. Designed to be easy to read contact/ info and also be appealing/interesting, unlike a traditional business card.

Industry/Entity Type

Landscape Construction

Contact Information for Business Card

Company name : Brambleford Landscape Construction, phone number: (877) 62Vista, website:Bramblefordyards.example, Email, sales@bramblefordyards.example

Requirements
Nice to have
• Luxurious finishes/ details…. Icons or emblems next to contact info
Should not have
• Clipart or general pictures

```html
<!DOCTYPE html>
<html lang="en">
<head>
<meta charset="utf-8">
<title>Brambleford Landscape Construction – Business Cards</title>
<link href="https://fonts.googleapis.com/css2?family=Cinzel:wght@400;600&family=Open+Sans:wght@400;600&display=swap" rel="stylesheet">
<style>
  :root {
    --backdrop: #e9e7e3;
    --card-dark: #121212;
    --card-light: #ffffff;
    --brand-blue: #3b7cc9;
    --brand-green: #8dc63f;
    --ink: #2a2a2a;
  }
  * { box-sizing: border-box; margin: 0; padding: 0; }
  html, body {
    width: 1200px; height: 913px; overflow: hidden;
    background: var(--backdrop);
  }
  .canvas { position: relative; width: 1200px; height: 913px; }

  .card {
    position: absolute; width: 520px; height: 297px;
    border-radius: 4px; overflow: hidden;
    box-shadow: 0 14px 30px rgba(0,0,0,.22);
  }

  /* Front – dark */
  .card--front {
    left: 50px; top: 110px;
    background: linear-gradient(135deg, #1c1c1c 0%, var(--card-dark) 60%);
    display: flex; flex-direction: column; align-items: center; justify-content: center;
    gap: 30px;
  }
  .wordmark {
    font-family: "Cinzel", serif; font-weight: 600;
    color: var(--brand-blue); text-align: center; line-height: 1.15;
  }
  .card--front .wordmark { font-size: 34px; }
  .card--front .wordmark small { display: block; font-size: 17px; letter-spacing: 3px; }
  .wordmark-dot {
    display: inline-block; width: 14px; height: 14px; border-radius: 50%;
    background: var(--brand-green); margin-bottom: 10px;
  }
  .front-url {
    font-family: "Cinzel", serif; font-size: 15px; letter-spacing: 2px;
    color: var(--brand-blue);
  }

  /* Back – light */
  .card--back {
    left: 630px; top: 500px;
    background: var(--card-light);
  }
  .card--back .wordmark {
    position: absolute; left: 22px; top: 118px; width: 210px;
    font-size: 21px;
  }
  .card--back .wordmark small { display: block; font-size: 11px; letter-spacing: 2px; }
  .card--back .wordmark-dot { width: 10px; height: 10px; margin-bottom: 6px; }

  .divider { position: absolute; left: 248px; top: 44px; width: 8px; height: 150px; }

  .contact {
    position: absolute; left: 272px; top: 38px; right: 14px;
    font-family: "Open Sans", sans-serif; font-size: 11px; color: var(--ink);
    line-height: 1.55;
  }
  .contact-name {
    font-family: "Cinzel", serif; font-weight: 600; font-size: 21px; line-height: 1.1;
    color: var(--brand-blue);
  }
  .contact-name span { color: var(--brand-green); }
  .contact-role { margin-bottom: 6px; }
  .contact-line { display: flex; align-items: center; gap: 6px; }
  .contact-line svg { flex: none; }

  .card-band {
    position: absolute; left: 0; right: 0; bottom: 0; height: 20px;
    background: var(--brand-green); border-top: 3px solid var(--brand-blue);
  }
</style>
</head>
<body>
<main class="canvas">

  <section class="card card--front" aria-label="Card front">
    <div class="wordmark">
      <span class="wordmark-dot"></span><br>
      Brambleford
      <small>Landscape Construction</small>
    </div>
    <p class="front-url">www.Bramblefordyards.example</p>
  </section>

  <section class="card card--back" aria-label="Card back">
    <div class="wordmark">
      <span class="wordmark-dot"></span><br>
      Brambleford
      <small>Landscape Construction</small>
    </div>

    <svg class="divider" viewBox="0 0 8 150" aria-hidden="true">
      <line x1="1" y1="0" x2="1" y2="150" stroke="#8dc63f" stroke-width="1"/>
      <line x1="5" y1="18" x2="5" y2="132" stroke="#3b7cc9" stroke-width="3"/>
    </svg>

    <div class="contact">
      <p class="contact-name">Owen <span>Hartley</span></p>
      <p class="contact-role">Director</p>
      <p>4127 Millbrook Valley Rd.,</p>
      <p>NUM 118, Fairhaven, OH 45210</p>
      <p class="contact-line">
        <svg width="10" height="10" viewBox="0 0 10 10" aria-hidden="true"><path d="M2 0.5 L4 2.8 L3 4 Q4.5 6 6 7 L7.2 6 L9.5 8 L8.3 9.5 Q3.5 9 0.5 1.7 Z" fill="#8dc63f"/></svg>
        (877) 62Vista
      </p>
      <p class="contact-line">
        <svg width="10" height="10" viewBox="0 0 10 10" aria-hidden="true"><rect x="0.5" y="2" width="9" height="6.5" fill="#8dc63f"/><path d="M0.5 2 L5 5.8 L9.5 2" fill="none" stroke="#fff" stroke-width="1"/></svg>
        sales@bramblefordyards.example
      </p>
      <p class="contact-line">
        <svg width="10" height="10" viewBox="0 0 10 10" aria-hidden="true"><circle cx="5" cy="5" r="4.5" fill="#8dc63f"/><path d="M1 5 H9 M5 0.5 Q2.5 5 5 9.5 M5 0.5 Q7.5 5 5 9.5" fill="none" stroke="#fff" stroke-width=".8"/></svg>
        www.bramblefordyards.example
      </p>
    </div>

    <div class="card-band"></div>
  </section>

</main>
</body>
</html>
```